Bref créative
Business cards and stationary Hospitality group company in Mexico
subtitle is optional "Hospitalidad Hecha en Casa"
I need double sided standard sized Business Card [3.5" x 2"]
I like the fonts used in my logo but we are open to new fonts or more than one if necessary
Modern
Armando Quiroz
4817 Almendros
Col. Brisa Verde
Monterrey, NL México
CP 58213
tavo@qelun.mx
www.qelun.mx
I am looking for a modern design, I like those colors but feel free to play with the colors if you have an idea..
RV DELCANTO

```html
<!DOCTYPE html>
<html lang="es">
<head>
<meta charset="utf-8">
<title>RV Delcanto — Papelería</title>
<link href="https://fonts.googleapis.com/css2?family=Montserrat:wght@400;600;700&display=swap" rel="stylesheet">
<style>
  :root{
    --bg:#ececec;
    --paper:#ffffff;
    --ink:#2b2a2a;
    --ink-soft:#3a3939;
    --orange:#f26a2e;
    --orange-deep:#e8462a;
    --grey-line:#8a8a8a;
    --text-light:#cfcfcf;
  }
  *{box-sizing:border-box;margin:0;padding:0}
  html,body{width:1200px;height:936px;overflow:hidden;background:var(--bg);font-family:'Montserrat',sans-serif}
  .canvas{position:relative;width:1200px;height:936px}
  .piece{position:absolute;background:var(--paper);box-shadow:0 2px 6px rgba(0,0,0,.12);overflow:hidden}

  .brand{font-weight:700;color:var(--orange);letter-spacing:.5px;display:flex;align-items:center;gap:6px;white-space:nowrap}
  .brand .dot{width:.55em;height:.55em;border-radius:50%;background:var(--orange)}

  .url-tab{position:absolute;right:0;background:linear-gradient(90deg,var(--orange),var(--orange-deep));color:#fff;font-weight:600;letter-spacing:2px;display:flex;align-items:center;justify-content:flex-end;clip-path:polygon(14% 0,100% 0,100% 100%,0 100%)}
  .url-tab b{font-weight:700}
  .rule{position:absolute;left:0;height:2px;background:linear-gradient(90deg,transparent,var(--grey-line))}

  .contact{position:absolute;font-size:7px;line-height:10px;color:var(--text-light);list-style:none}
  .contact li{display:flex;align-items:center;gap:5px}
  .contact li::before{content:"";width:4px;height:4px;background:var(--orange)}

  /* Letterhead */
  .letterhead{left:190px;top:63px;width:381px;height:559px}
  .letterhead .head{position:absolute;inset:0 0 auto 0;height:84px;background:var(--ink)}
  .letterhead .head .brand{position:absolute;left:22px;top:32px;font-size:18px}
  .letterhead .contact{left:280px;top:14px}
  .letterhead .watermark{position:absolute;left:0;right:0;top:230px;text-align:center;font-size:44px;font-weight:700;color:var(--orange);opacity:.12}
  .letterhead .rule{bottom:26px;width:250px}
  .letterhead .url-tab{bottom:14px;height:26px;width:160px;padding-right:14px;font-size:10px}

  /* Folder */
  .folder{left:634px;top:38px;width:432px;height:584px;background:var(--ink)}
  .folder .brand{position:absolute;left:0;right:0;top:262px;justify-content:center;font-size:40px}
  .folder .foot{position:absolute;left:0;right:0;bottom:0;height:38px;background:var(--paper)}
  .folder .url-tab{bottom:22px;height:30px;width:220px;padding-right:18px;font-size:11px}

  /* Business cards */
  .card-front{left:43px;top:665px;width:180px;height:86px}
  .card-front .top{position:absolute;inset:0 0 auto 0;height:50px;background:var(--ink)}
  .card-front .top .brand{position:absolute;left:10px;top:16px;font-size:12px}
  .card-front .name{position:absolute;right:0;top:22px;background:var(--orange);color:#fff;font-size:6px;font-weight:600;padding:2px 6px}
  .card-front .details{position:absolute;left:10px;top:54px;font-size:5px;line-height:7px;color:var(--ink-soft)}
  .card-front .url{position:absolute;right:10px;bottom:6px;font-size:6px;font-weight:700;color:var(--orange)}
  .card-back{left:43px;top:774px;width:180px;height:106px;background:var(--ink)}
  .card-back .brand{position:absolute;left:16px;top:42px;font-size:16px}

  /* Envelope DL */
  .envelope{left:259px;top:672px;width:439px;height:208px}
  .envelope .head{position:absolute;inset:0 0 auto 0;height:82px;background:var(--ink)}
  .envelope .head .brand{position:absolute;left:20px;top:20px;font-size:18px}
  .envelope .head .addr{position:absolute;left:20px;top:52px;font-size:6px;line-height:9px;color:var(--text-light)}
  .envelope .rule{bottom:20px;width:240px}
  .envelope .url-tab{bottom:6px;height:26px;width:190px;padding-right:16px;font-size:11px}

  /* Envelope back */
  .envelope-back{left:736px;top:672px;width:431px;height:208px}
  .envelope-back .flap{position:absolute;inset:0 0 auto 0;height:62px;background:linear-gradient(180deg,var(--orange-deep),var(--orange));border-radius:0 0 50% 50%/0 0 40% 40%;display:flex;align-items:center;justify-content:center;color:#fff;font-size:12px;letter-spacing:2px}
  .envelope-back .flap b{font-weight:700}
</style>
</head>
<body>
<main class="canvas">

  <section class="piece letterhead">
    <header class="head">
      <div class="brand"><span class="dot"></span>Delcanto</div>
    </header>
    <ul class="contact">
      <li>4817 Almendros</li>
      <li>Col. Brisa Verde</li>
      <li>Monterrey, NL México</li>
      <li>CP 58213</li>
      <li>tavo@qelun.mx</li>
    </ul>
    <div class="watermark">Delcanto</div>
    <div class="rule"></div>
    <div class="url-tab">www.<b>qelun</b>.mx</div>
  </section>

  <section class="piece folder">
    <div class="brand"><span class="dot"></span>Delcanto</div>
    <div class="foot"></div>
    <div class="url-tab">www.<b>qelun</b>.mx</div>
  </section>

  <section class="piece card-front">
    <div class="top">
      <div class="brand"><span class="dot"></span>Delcanto</div>
      <div class="name">Armando Quiroz</div>
    </div>
    <div class="details">Tel. +52 81 5550 1234<br>tavo@qelun.mx</div>
    <div class="url">www.qelun.mx</div>
  </section>

  <section class="piece card-back">
    <div class="brand"><span class="dot"></span>Delcanto</div>
  </section>

  <section class="piece envelope">
    <header class="head">
      <div class="brand"><span class="dot"></span>Delcanto</div>
      <div class="addr">4817 Almendros, Col. Brisa Verde, Monterrey, NL México, CP 58213</div>
    </header>
    <div class="rule"></div>
    <div class="url-tab">www.<b>qelun</b>.mx</div>
  </section>

  <section class="piece envelope-back">
    <div class="flap">www.<b>qelun</b>.mx</div>
  </section>

</main>
</body>
</html>
```